Heron Loan Partners Business Card

We need a business card design for our mortgage servicing company. In addition to servicing the loans of homeowners, we help homeowners with purchasing their homes and any mortgage refinancing. We would like to see designs that use the colors in the logo attached below (gold-ish yellow and navy blue), and any other design you deem fit! The design should communicate a simpler life with smart mortgages provided by Heron.

```html
<!DOCTYPE html>
<html lang="en">
<head>
<meta charset="utf-8">
<title>Heron Loan Partners Business Card</title>
<link href="https://fonts.googleapis.com/css2?family=Roboto:wght@400;500;700&display=swap" rel="stylesheet">
<style>
  :root {
    --navy: #251f5a;
    --gold: #d9a92f;
    --paper: #f7f7f5;
    --ink: #1d1d1f;
    --backdrop: #2c2c2f;
  }
  * { box-sizing: border-box; margin: 0; padding: 0; }
  html, body { width: 1200px; height: 779px; overflow: hidden; }
  body {
    background: var(--backdrop);
    font-family: "Roboto", Arial, sans-serif;
    position: relative;
  }
  .card { position: absolute; box-shadow: 0 8px 24px rgba(0,0,0,.45); }

  /* Front */
  .card-front {
    left: 60px; top: 150px; width: 560px; height: 320px;
    background: var(--navy);
    display: flex; flex-direction: column; align-items: center; justify-content: center;
  }
  .brand { display: flex; align-items: center; gap: 14px; color: var(--gold); }
  .brand-dot { width: 18px; height: 18px; border-radius: 50%; background: var(--gold); }
  .brand-name { font-weight: 700; font-size: 40px; letter-spacing: .5px; }
  .front-web {
    margin-top: 70px; color: #fff; font-size: 14px; letter-spacing: 4px;
  }
  .front-web .accent { color: var(--gold); }

  /* Back */
  .card-back {
    left: 760px; top: 110px; width: 320px; height: 560px;
    background: var(--paper);
    padding: 48px 40px;
    color: var(--ink);
  }
  .back-brand { color: var(--gold); font-weight: 700; font-size: 22px; display: flex; align-items: center; gap: 10px; }
  .back-brand .brand-dot { width: 12px; height: 12px; }
  .person-name { margin-top: 36px; color: var(--gold); font-weight: 700; font-size: 24px; }
  .person-title { margin-top: 4px; color: var(--navy); font-size: 16px; }
  .icon-row { margin-top: 18px; display: flex; align-items: center; gap: 6px; }
  .icon-row .rule { width: 18px; height: 1px; background: var(--ink); }
  .icon { width: 22px; height: 22px; border-radius: 50%; background: var(--gold); display: flex; align-items: center; justify-content: center; }
  .contact { margin-top: 14px; font-size: 16px; line-height: 1.35; }
  .divider { margin: 22px 0; width: 110px; height: 2px; background: var(--ink); }
  .address { font-size: 16px; line-height: 1.35; }
  .tagline { position: absolute; left: 40px; bottom: 48px; font-size: 16px; }
</style>
</head>
<body>
  <section class="card card-front">
    <div class="brand">
      <span class="brand-dot"></span>
      <span class="brand-name">Heron Loan Partners</span>
    </div>
    <p class="front-web">www.<span class="accent">Heron</span>.com</p>
  </section>

  <section class="card card-back">
    <div class="back-brand"><span class="brand-dot"></span>Heron Loan Partners</div>
    <h1 class="person-name">Owen Hartley</h1>
    <p class="person-title">President</p>
    <div class="icon-row">
      <span class="rule"></span>
      <span class="icon"><svg width="12" height="12" viewBox="0 0 24 24"><path fill="#fff" d="M6.6 10.8a15 15 0 0 0 6.6 6.6l2.2-2.2c.3-.3.7-.4 1-.2 1.1.4 2.3.6 3.6.6.6 0 1 .4 1 1V20c0 .6-.4 1-1 1A17 17 0 0 1 3 4c0-.6.4-1 1-1h3.5c.6 0 1 .4 1 1 0 1.3.2 2.5.6 3.6.1.3 0 .7-.2 1z"/></svg></span>
      <span class="icon"><svg width="12" height="12" viewBox="0 0 24 24"><path fill="#fff" d="M3 5h18v14H3z"/><path fill="none" stroke="#d9a92f" stroke-width="2" d="M3 6l9 7 9-7"/></svg></span>
      <span class="icon"><svg width="12" height="12" viewBox="0 0 24 24"><circle cx="12" cy="12" r="9" fill="none" stroke="#fff" stroke-width="2"/><path fill="none" stroke="#fff" stroke-width="2" d="M3 12h18M12 3c3 3 3 15 0 18M12 3c-3 3-3 15 0 18"/></svg></span>
      <span class="rule"></span>
    </div>
    <div class="contact">
      <p>(555) 0142-7781</p>
      <p>name@heron.com</p>
      <p>www.heron.com</p>
    </div>
    <div class="divider"></div>
    <div class="address">
      <p>2710 Larchmont Avenue</p>
      <p>Bayside Hollow, NY 10990</p>
    </div>
    <p class="tagline">Simpler life with smart mortgages</p>
  </section>
</body>
</html>
```